Website 950x200 Header w/ logo

I'm in need of a website header for a new site called DaysofMarlo.com

The site is basically a glorified blog for myself to write my thoughts about politics, sports, TV shows, current events, whatever. I have a lot of interests.

The site is going to look very very similar to http://www.brisknetmaker.example/4093817/8-ways-to-win-the-race-for-creative-talent

but instead of having a dynamic header that becomes the picture with each article, its just going to be a static header in which I'd like to have the name of the site (Days of Marlo) and some kind of logo, pictures, etc - I'm totally open to anything. The only thing is it needs to have a dark (probably black) background and needs to be 950x200px.

I envision a black background, with gray and white as the primary colors and then some secondary colors potentially, but again I'm open to anything as long as it's on the black background or some kind of charcoal gray or wahtever. On the site the black part will go all the way from the left of the screen to the right no matter what the window size, but I'd like to keep all the content inside of 950x200px

email me marlo.pettigrew@inboxly.example if you have any questions. Thanks!

Industry/Entity Type

Tv

```html
<!DOCTYPE html>
<html lang="en">
<head>
<meta charset="utf-8">
<title>Days of Marlo</title>
<link rel="stylesheet" href="https://fonts.googleapis.com/css2?family=Kaushan+Script&display=swap">
<style>
  :root {
    --night: #000000;
    --charcoal: #1c1c1c;
    --smoke: #262626;
    --grass: #141414;
    --title-white: #ffffff;
  }
  html, body {
    margin: 0;
    padding: 0;
    width: 1200px;
    height: 253px;
    overflow: hidden;
    background: var(--night);
  }
  .site-header {
    position: relative;
    width: 1200px;
    height: 253px;
    background: var(--night);
    overflow: hidden;
  }
  .header-art {
    position: absolute;
    inset: 0;
    width: 1200px;
    height: 253px;
  }
  .site-title {
    position: absolute;
    left: 22px;
    top: 92px;
    margin: 0;
    font-family: "Kaushan Script", cursive;
    font-weight: 400;
    font-size: 118px;
    line-height: 1;
    letter-spacing: 4px;
    color: var(--title-white);
    white-space: nowrap;
  }
</style>
</head>
<body>
  <header class="site-header">
    <svg class="header-art" viewBox="0 0 1200 253" xmlns="http://www.w3.org/2000/svg">
      <defs>
        <linearGradient id="brush-band" x1="0" y1="0" x2="1" y2="0">
          <stop offset="0" stop-color="var(--charcoal)"/>
          <stop offset="0.75" stop-color="var(--smoke)"/>
          <stop offset="1" stop-color="var(--night)"/>
        </linearGradient>
        <linearGradient id="grass-field" x1="0" y1="0" x2="0" y2="1">
          <stop offset="0" stop-color="var(--night)"/>
          <stop offset="1" stop-color="var(--grass)"/>
        </linearGradient>
      </defs>
      <g class="brush-stroke-band" role="img" aria-label="Dark grey painted brush stroke texture across the top of the header">
        <rect x="0" y="0" width="1200" height="40" fill="url(#brush-band)"/>
        <path d="M0 40 H1040 V70 H860 V88 H560 V60 H0 Z" fill="url(#brush-band)"/>
      </g>
      <rect class="grass-silhouette" role="img" aria-label="Faint dark grass blades silhouetted along the bottom edge" x="0" y="170" width="1200" height="83" fill="url(#grass-field)"/>
    </svg>
    <h1 class="site-title">Days of Marlo</h1>
  </header>
</body>
</html>
```